Website for "Nodo de Soluciones Verdantes"

We need a new web design for an enterprise dedicated to environment and energy saving engineering, based in Monterrey, Mexico.
They offer consulting services, mainly to enhance building designs, and they are also resellers for several products in the energy saving field.

The final design should be oriented to engineers and architects, and should communicate professionalism, innovation, environment care.

Here is the website of a partner enterprise, which does pretty much the same:

http://www.cirelumen.com/

Target Market(s)

mainly architects and engineers looking for solutions on energy efficiency building

Industry/Entity Type

Environment

Requirements
Must have
• Entry page must be quite graphical and intuitive, must have a "products listing" and a "projects portfolio".

```html
<!DOCTYPE html>
<html lang="en">
<head>
<meta charset="utf-8">
<title>Nodo de Soluciones Verdantes</title>
<link href="https://fonts.googleapis.com/css2?family=Source+Sans+3:wght@400;600;700&display=swap" rel="stylesheet">
<style>
:root{
  --teal:#13b8be;
  --teal-dark:#0c9ca2;
  --teal-line:#0fa6ac;
  --orange:#f47520;
  --ink:#3a3a3a;
  --ink-soft:#555;
  --navy:#3b3a70;
  --footer:#252525;
  --page:#ffffff;
  --line:#e3e3e3;
}
*{box-sizing:border-box;margin:0;padding:0}
html,body{width:1070px;height:1200px;overflow:hidden;background:var(--page);font-family:"Source Sans 3",Arial,sans-serif;color:var(--ink)}
.page{position:relative;width:1070px;height:1200px}
.abs{position:absolute}

/* header */
.brand{left:77px;top:36px;display:flex;align-items:center;gap:12px}
.brand-dot{width:50px;height:50px;border-radius:50%;background:var(--teal)}
.brand-name{font-size:21px;font-weight:600;color:var(--ink-soft);line-height:1.1;width:180px}
.call{right:78px;top:22px;font-size:15px;font-weight:600;color:var(--navy)}
.search{left:791px;top:61px;width:201px;height:30px;border:1px solid #ccc;border-radius:3px;display:flex;align-items:center;justify-content:space-between;padding:0 8px;font-size:12px;font-style:italic;color:#999}

/* nav */
.nav{left:77px;top:113px;width:915px;height:43px;background:linear-gradient(#1cc4ca,var(--teal-dark));border-radius:4px;display:flex;list-style:none}
.nav li{color:#fff;font-size:15px;font-weight:600;line-height:43px;padding:0 13px;border-right:1px solid var(--teal-line);white-space:nowrap}
.nav li:nth-child(1){width:73px}
.nav li:nth-child(2){width:95px;padding-left:26px}
.nav li:nth-child(3){width:117px;padding-left:23px}
.nav li:nth-child(4){width:106px;padding-left:23px}
.nav li:nth-child(5){width:153px;padding-left:24px}
.nav li:nth-child(6){width:81px;padding-left:23px}
.nav li:nth-child(7){width:183px;padding-left:23px}
.nav li:nth-child(8){border-right:none;padding-left:23px}

/* hero */
.hero{left:77px;top:165px;width:915px;height:386px;background:linear-gradient(180deg,#7fb4e4 0%,#a8cce0 38%,#7ea83c 62%,#5f8f1f 100%)}
.hero-caption{left:107px;top:415px;width:357px;height:104px;background:rgba(40,40,30,.78);color:#fff;padding:12px 16px}
.hero-caption h2{font-size:18px;font-weight:600;margin-bottom:6px}
.hero-caption p{font-size:13.5px;line-height:22px}
.hero-arrows{left:915px;top:516px;display:flex;gap:4px}
.hero-arrows span{width:27px;height:26px;background:#4a5a17;display:flex;align-items:center;justify-content:center}

/* features */
.feature{top:592px;width:275px}
.feature .head{display:flex;gap:14px;align-items:flex-start}
.feature h3{font-size:21px;font-weight:400;color:var(--ink)}
.feature h4{font-size:14px;font-weight:600;color:var(--ink);margin-top:2px}
.feature p{font-size:12px;line-height:19px;color:var(--ink-soft);margin-top:14px;padding-left:5px}

/* products */
.section-title{font-size:18px;font-weight:600;color:var(--ink)}
.products{left:77px;top:800px;width:263px;list-style:none;box-shadow:0 2px 4px rgba(0,0,0,.15)}
.products li{height:42.8px;display:flex;align-items:center;justify-content:space-between;padding:0 14px 0 16px;font-size:16px;color:var(--ink);background:linear-gradient(#fff,#f1fafa);border-bottom:1px solid var(--line)}
.products li.active{background:var(--orange);color:#fff}
.chev{width:22px;height:22px;border-radius:50%;border:1px solid #ddd;background:#fff;display:flex;align-items:center;justify-content:center}
.active .chev{background:#333;border-color:#333}

/* portfolio */
.pf-arrows{left:950px;top:763px;display:flex;gap:3px}
.pf-arrows span{width:18px;height:18px;border-radius:50%;background:#8a8a8a;display:flex;align-items:center;justify-content:center}
.card{top:800px;width:263px}
.card .photo{height:160px;border:4px solid #e6e6e6}
.card h5{font-size:13.5px;font-weight:700;line-height:19px;margin-top:15px;color:var(--ink)}
.card p{font-size:12px;line-height:19px;color:var(--ink-soft);margin-top:4px}

/* footer */
.footer{left:0;top:1099px;width:1070px;height:101px;background:var(--footer);color:#ddd}
.footer-links{left:76px;top:24px;font-size:12px}
.copy{left:77px;top:56px;font-size:12px}
.social{left:566px;top:28px;display:flex;gap:10px}
.social span{width:28px;height:28px;border-radius:4px;background:#6a6a6a}
.newsletter{left:722px;top:32px;font-size:14px;color:#fff}
.news-field{left:805px;top:28px;width:181px;height:30px;background:#fff;border-radius:2px;display:flex;align-items:center;justify-content:flex-end;padding-right:8px;color:#777;font-size:16px}
</style>
</head>
<body>
<div class="page">

  <header>
    <div class="abs brand">
      <span class="brand-dot"></span>
      <span class="brand-name">Nodo de Soluciones Verdantes</span>
    </div>
    <div class="abs call">Call me : +52 555 410 782</div>
    <div class="abs search">Search..
      <svg width="13" height="13" viewBox="0 0 13 13"><circle cx="5.5" cy="5.5" r="4" fill="none" stroke="#999" stroke-width="1.8"/><line x1="8.5" y1="8.5" x2="12" y2="12" stroke="#999" stroke-width="2"/></svg>
    </div>
  </header>

  <ul class="abs nav">
    <li>HOME</li><li>ABOUT</li><li>PRODUCTS</li><li>SERVICES</li><li>ENERGY SAVING</li><li>BLOG</li><li>PROJECT PORTFOLIOS</li><li>CONTACT</li>
  </ul>

  <section class="abs hero" role="img" aria-label="Photo of a green globe wrapped in grass recycling arrows on a meadow under blue sky"></section>
  <div class="abs hero-caption">
    <h2>Amet dolor sit tation ullamcorper</h2>
    <p>Donec id ante magna. Nullam sollicitudin, ipsum vel hendrerit aliquam, nisi sapien pellentesque odio.</p>
  </div>
  <div class="abs hero-arrows">
    <span><svg width="10" height="12" viewBox="0 0 10 12"><polyline points="7,1 2,6 7,11" fill="none" stroke="#fff" stroke-width="2"/></svg></span>
    <span><svg width="10" height="12" viewBox="0 0 10 12"><polyline points="3,1 8,6 3,11" fill="none" stroke="#fff" stroke-width="2"/></svg></span>
  </div>

  <section>
    <div class="abs feature" style="left:77px">
      <div class="head">
        <svg width="50" height="54" viewBox="0 0 50 54"><g fill="var(--teal)"><rect x="2" y="36" width="9" height="17"/><rect x="14" y="28" width="9" height="25"/><rect x="26" y="33" width="9" height="20"/><rect x="38" y="20" width="9" height="33"/></g><polyline points="2,28 16,14 28,24 44,6" fill="none" stroke="var(--teal)" stroke-width="4"/><polygon points="36,2 48,0 46,12" fill="var(--teal)"/></svg>
        <div><h3>Energy Analysis</h3><h4>Lorem Ipsum dolore</h4></div>
      </div>
      <p>Scing elit vivamus faucibus, mi quis convallisto te mpus, magna elit tincidunt arcu, ac rutrumop tell us nisl sed nisi. Morbi tempor quam vel massa.</p>
    </div>
    <div class="abs feature" style="left:398px">
      <div class="head">
        <svg width="50" height="54" viewBox="0 0 50 54"><g fill="var(--teal)"><circle cx="20" cy="20" r="14"/><g stroke="var(--teal)" stroke-width="6"><line x1="20" y1="2" x2="20" y2="38"/><line x1="2" y1="20" x2="38" y2="20"/><line x1="7" y1="7" x2="33" y2="33"/><line x1="33" y1="7" x2="7" y2="33"/></g><circle cx="38" cy="42" r="7"/><g stroke="var(--teal)" stroke-width="3"><line x1="38" y1="32" x2="38" y2="52"/><line x1="28" y1="42" x2="48" y2="42"/></g></g><circle cx="20" cy="20" r="5" fill="#fff"/><circle cx="38" cy="42" r="2.5" fill="#fff"/></svg>
        <div><h3>New Solutions</h3><h4>Lorem Ipsum dolore</h4></div>
      </div>
      <p>Scing elit vivamus faucibus, mi quis convallisto te mpus, magna elit tincidunt arcu, ac rutrumop tell us nisl sed nisi. Morbi tempor quam vel massa.</p>
    </div>
    <div class="abs feature" style="left:730px">
      <div class="head">
        <svg width="50" height="54" viewBox="0 0 50 54"><path d="M6 48 C2 30 14 8 44 6 C48 30 34 46 12 44 Z" fill="var(--teal)"/><path d="M4 52 L30 22" stroke="#fff" stroke-width="2.5"/></svg>
        <div><h3>Energy Saving</h3><h4>Lorem Ipsum dolore</h4></div>
      </div>
      <p>Scing elit vivamus faucibus, mi quis convallisto te mpus, magna elit tincidunt arcu, ac rutrumop tell us nisl sed nisi. Morbi tempor quam vel massa.</p>
    </div>
  </section>

  <h2 class="abs section-title" style="left:77px;top:760px">Products</h2>
  <ul class="abs products">
    <li class="active">Recent Posts<span class="chev"><svg width="8" height="8" viewBox="0 0 8 8"><path d="M1 4h5M4 2l2 2-2 2" fill="none" stroke="#fff" stroke-width="1.2"/></svg></span></li>
    <li>Energy Resources<span class="chev"><svg width="8" height="8" viewBox="0 0 8 8"><path d="M1 4h5M4 2l2 2-2 2" fill="none" stroke="#555" stroke-width="1.2"/></svg></span></li>
    <li>Phasellus congue<span class="chev"><svg width="8" height="8" viewBox="0 0 8 8"><path d="M1 4h5M4 2l2 2-2 2" fill="none" stroke="#555" stroke-width="1.2"/></svg></span></li>
    <li>Nulla faucibus nibh<span class="chev"><svg width="8" height="8" viewBox="0 0 8 8"><path d="M1 4h5M4 2l2 2-2 2" fill="none" stroke="#555" stroke-width="1.2"/></svg></span></li>
    <li>Suspendisse dictum dolor<span class="chev"><svg width="8" height="8" viewBox="0 0 8 8"><path d="M1 4h5M4 2l2 2-2 2" fill="none" stroke="#555" stroke-width="1.2"/></svg></span></li>
    <li>Proin dolor justo<span class="chev"><svg width="8" height="8" viewBox="0 0 8 8"><path d="M1 4h5M4 2l2 2-2 2" fill="none" stroke="#555" stroke-width="1.2"/></svg></span></li>
  </ul>

  <h2 class="abs section-title" style="left:423px;top:761px">Projects Portfolio</h2>
  <div class="abs pf-arrows">
    <span><svg width="8" height="10" viewBox="0 0 8 10"><polyline points="6,1 2,5 6,9" fill="none" stroke="#fff" stroke-width="2"/></svg></span>
    <span><svg width="8" height="10" viewBox="0 0 8 10"><polyline points="2,1 6,5 2,9" fill="none" stroke="#fff" stroke-width="2"/></svg></span>
  </div>
  <article class="abs card" style="left:423px">
    <div class="photo" role="img" aria-label="Photo of a hand holding a light bulb in front of a chalk recycling symbol on a green board" style="background:linear-gradient(135deg,#3f8a3a,#2e6e2c)"></div>
    <h5>There are many variations anythin emba rss true generator on Internet.</h5>
    <p>Nunc venenatis lacinia lacus quis vulputate. Susp endisse imperdiet leo sed urna molestie.</p>
  </article>
  <article class="abs card" style="left:729px">
    <div class="photo" role="img" aria-label="Photo of a finger pressing a light switch on patterned green wallpaper" style="background:linear-gradient(135deg,#6f7a55,#b9b4a6)"></div>
    <h5>There are many variations anythin emba rss true generator on Internet.</h5>
    <p>Nunc venenatis lacinia lacus quis vulputate. Susp endisse imperdiet leo sed urna molestie.</p>
  </article>

  <footer class="abs footer">
    <div class="abs footer-links">Home | About | Products | Services | Energy Saving | Blog | Project Portfolios | Contact</div>
    <div class="abs copy">Copyrights 2013. All Rights Reserved.</div>
    <div class="abs social"><span></span><span></span><span></span></div>
    <div class="abs newsletter">Newsletter</div>
    <div class="abs news-field">&#8250;&#8250;</div>
  </footer>

</div>
</body>
</html>
```